Im open to ideas.. I was thinking on my business cards aswell as my logo. a place for my name. email. phone number and abn..

ive attched a file with my business logo. which i dont love the colours.. i was think a dark background with charcoal letters so something along those colour schumes but im open to ideas..

BRM Constructions

```html
<!DOCTYPE html>
<html lang="en">
<head>
<meta charset="utf-8">
<title>BRM Constructions – Business Card</title>
<link rel="stylesheet" href="https://fonts.googleapis.com/css2?family=Lato:wght@400;700;900&display=swap">
<style>
  :root {
    --backdrop: #2a2a2a;
    --card: #f4f4f4;
    --ink: #231f20;
    --ink-soft: #3a3a3a;
    --accent: #d7141f;
  }
  * { margin: 0; padding: 0; box-sizing: border-box; }
  html, body {
    width: 1200px;
    height: 873px;
    overflow: hidden;
    background: var(--backdrop);
    font-family: "Lato", Arial, sans-serif;
  }
  .business-card {
    position: absolute;
    left: 150px;
    top: 162px;
    width: 900px;
    height: 548px;
    background: var(--card);
    border-radius: 22px;
    color: var(--ink);
    overflow: hidden;
  }
  .brand {
    position: absolute;
    left: 130px;
    top: 140px;
    display: flex;
    align-items: center;
    gap: 16px;
    white-space: nowrap;
  }
  .brand-mark {
    width: 30px;
    height: 30px;
    background: var(--accent);
    flex: none;
  }
  .brand-name {
    font-weight: 900;
    font-size: 46px;
    letter-spacing: 1px;
    text-transform: uppercase;
    color: var(--ink);
    line-height: 1;
  }
  .holder {
    position: absolute;
    right: 80px;
    top: 250px;
    text-align: right;
  }
  .holder-name {
    font-weight: 700;
    font-size: 26px;
    color: var(--accent);
  }
  .holder-role {
    font-size: 17px;
    color: var(--ink-soft);
    margin-top: 2px;
  }
  .contacts {
    position: absolute;
    left: 80px;
    bottom: 60px;
    list-style: none;
  }
  .contact {
    display: flex;
    align-items: center;
    gap: 10px;
    font-size: 21px;
    color: var(--ink-soft);
    margin-top: 12px;
  }
  .contact svg { width: 20px; height: 20px; flex: none; }
  .contact-web {
    font-weight: 900;
    font-size: 24px;
    color: var(--accent);
    margin-top: 18px;
  }
</style>
</head>
<body>
  <article class="business-card">
    <div class="brand">
      <span class="brand-mark"></span>
      <span class="brand-name">BRM Constructions</span>
    </div>

    <div class="holder">
      <p class="holder-name">Daniel Hartley</p>
      <p class="holder-role">Owner / Founder</p>
    </div>

    <ul class="contacts">
      <li class="contact">
        <svg viewBox="0 0 24 24" aria-hidden="true"><path fill="#d7141f" d="M6.6 10.8a15.1 15.1 0 0 0 6.6 6.6l2.2-2.2a1 1 0 0 1 1-.25 11.4 11.4 0 0 0 3.6.57 1 1 0 0 1 1 1V20a1 1 0 0 1-1 1A17 17 0 0 1 3 4a1 1 0 0 1 1-1h3.5a1 1 0 0 1 1 1c0 1.25.2 2.45.57 3.6a1 1 0 0 1-.25 1z"/></svg>
        <span>0400123456</span>
      </li>
      <li class="contact">
        <svg viewBox="0 0 24 24" aria-hidden="true"><rect x="2" y="5" width="20" height="14" rx="1.5" fill="#d7141f"/><path d="M3 6.5l9 7 9-7" fill="none" stroke="#f4f4f4" stroke-width="1.8"/></svg>
        <span>info@brmconstructions.com</span>
      </li>
      <li class="contact contact-web">www.brmconstructions.com</li>
    </ul>
  </article>
</body>
</html>
```